Harbor Crestline (Business Card Design)

Need business cards designed. Something modern, chic, and sleek. Mabye the back of the card should be the navy blue that is in the logo and then just the logo on the back.

Target Market(s)

Those in the hotel, office, and renovation industry

Contact Information for Business Card

1. Logo 2. Dorian Fenwick 3. CEO/Founder 4. Phone: (833) HarbCre / (833) 427-2731 5. Email: dorian@theharborcrestline.com 6. Website: www.theharborcrestline.com

Font styles to use
Other font styles liked:
• Look at the logo font and base the font for everything else off of that.

Colors
0054AA
0677BA
7BADD7
CADEEF
E8F1F8

Requirements
Must have
• Colors that are associated in the logo
Nice to have
• Sleek modern clean and chic design.

```html
<!DOCTYPE html>
<html lang="en">
<head>
<meta charset="utf-8">
<title>Harbor Crestline — Business Card</title>
<link href="https://fonts.googleapis.com/css2?family=Open+Sans:wght@400;600;700&display=swap" rel="stylesheet">
<style>
  :root {
    --stage: #e6e7ea;
    --navy: #0c1842;
    --navy-soft: #1b2a63;
    --gold: #c9a13b;
    --white: #ffffff;
    --muted: #d9deea;
  }
  * { box-sizing: border-box; margin: 0; padding: 0; }
  html, body { width: 1200px; height: 780px; overflow: hidden; }
  body {
    background: var(--stage);
    font-family: "Open Sans", sans-serif;
    position: relative;
  }
  .card {
    position: absolute;
    top: 240px;
    width: 520px;
    height: 300px;
    border-radius: 22px;
    background: var(--navy);
    overflow: hidden;
  }
  .card--front { left: 60px; }
  .card--back { left: 620px; }

  .brand {
    position: absolute;
    display: flex;
    align-items: center;
    gap: 10px;
  }
  .brand__mark { display: block; }
  .brand__name {
    font-weight: 700;
    text-transform: uppercase;
    letter-spacing: 0.06em;
    line-height: 1;
  }
  .card--front .brand { left: 34px; top: 34px; }
  .card--front .brand__name { color: var(--white); font-size: 20px; }
  .card--front .brand__mark { width: 14px; height: 14px; background: var(--gold); }

  .contact {
    position: absolute;
    left: 34px;
    top: 120px;
    color: var(--white);
    font-size: 12.5px;
    line-height: 1.55;
  }
  .contact__address { margin-bottom: 10px; }
  .contact__row { display: flex; align-items: center; gap: 8px; }
  .contact__icon { width: 12px; height: 12px; flex: none; }

  .person {
    position: absolute;
    right: 54px;
    top: 112px;
    text-align: right;
  }
  .person__name {
    color: var(--gold);
    font-weight: 700;
    font-size: 26px;
    line-height: 1.1;
  }
  .person__name strong { color: var(--white); font-weight: 700; }
  .person__title {
    color: var(--white);
    font-size: 13px;
    margin-top: 4px;
  }

  .accent-steps { position: absolute; right: 0; top: 120px; }

  .card--back .brand {
    left: 50%;
    top: 50%;
    transform: translate(-50%, -50%);
  }
  .card--back .brand__name { color: var(--navy-soft); font-size: 28px; }
  .card--back .brand__mark { width: 18px; height: 18px; background: var(--navy-soft); }
</style>
</head>
<body>

<section class="card card--front" aria-label="Business card front">
  <div class="brand">
    <span class="brand__mark"></span>
    <span class="brand__name">Harbor Crestline</span>
  </div>

  <div class="contact">
    <p class="contact__address">4120 Larkmoor Ave<br>Suite 210, Easton, MD 21601</p>
    <p class="contact__row">
      <svg class="contact__icon" viewBox="0 0 24 24" aria-hidden="true"><path fill="#c9a13b" d="M6.6 10.8a15.1 15.1 0 0 0 6.6 6.6l2.2-2.2c.3-.3.7-.4 1-.2 1.1.4 2.3.6 3.6.6.6 0 1 .4 1 1V20c0 .6-.4 1-1 1A17 17 0 0 1 3 4c0-.6.4-1 1-1h3.5c.6 0 1 .4 1 1 0 1.3.2 2.5.6 3.6.1.3 0 .7-.2 1z"/></svg>
      (833) HarbCre / (833) 427-2731
    </p>
    <p class="contact__row">
      <svg class="contact__icon" viewBox="0 0 24 24" aria-hidden="true"><circle cx="12" cy="12" r="9" fill="none" stroke="#c9a13b" stroke-width="2"/><path d="M3 12h18M12 3c3 3.5 3 14.5 0 18M12 3c-3 3.5-3 14.5 0 18" fill="none" stroke="#c9a13b" stroke-width="1.6"/></svg>
      www.theharborcrestline.com
    </p>
    <p class="contact__row">
      <svg class="contact__icon" viewBox="0 0 24 24" aria-hidden="true"><rect x="3" y="5" width="18" height="14" rx="1.5" fill="none" stroke="#c9a13b" stroke-width="2"/><path d="M3.5 6l8.5 7 8.5-7" fill="none" stroke="#c9a13b" stroke-width="2"/></svg>
      dorian@theharborcrestline.com
    </p>
  </div>

  <div class="person">
    <p class="person__name">Dorian <strong>Fenwick</strong></p>
    <p class="person__title">CEO/Founder</p>
  </div>

  <svg class="accent-steps" width="40" height="70" viewBox="0 0 40 70" aria-hidden="true">
    <rect x="22" y="0" width="18" height="22" fill="#c9a13b"/>
    <rect x="14" y="24" width="26" height="22" fill="#c9a13b"/>
    <rect x="24" y="48" width="16" height="22" fill="#c9a13b"/>
  </svg>
</section>

<section class="card card--back" aria-label="Business card back">
  <div class="brand">
    <span class="brand__mark"></span>
    <span class="brand__name">Harbor Crestline</span>
  </div>
</section>

</body>
</html>
```